Web Developer Needs a Business Card Design

I need a personal business card design that represents me as a web developer for potential employers. I would like the background to be a dark color on the front for contrast with my logo and name. The back will have all my information along with a smaller version of the logo. I want something with a modern look and feel, not too conservative. This will be used for potential employers and freelance work.

Industry/Entity Type

Business

Contact Information for Business Card

Front should have my logo and name. The back should have all my personal information which would include: name: Tom Varulek, phone: 570-614-3098, email: tomvarulek@quillbox.net, website url: www.tomvarulek.net, logo, web developer.

Font styles to use
Sans Serif

Requirements
Must have
• Must include my logo. The color palette base color will be the logo color.

```html
<!DOCTYPE html>
<html lang="en">
<head>
<meta charset="utf-8">
<title>Tom Varulek – Business Card</title>
<link rel="stylesheet" href="https://fonts.googleapis.com/css2?family=Open+Sans:wght@400;600&display=swap">
<style>
  :root {
    --teal: #6fcbb6;
    --ink: #111111;
    --ink-soft: #2a2a2a;
    --card: #ffffff;
    --backdrop: #e9e6e1;
  }
  * { margin: 0; padding: 0; box-sizing: border-box; }
  html, body { width: 1200px; height: 892px; overflow: hidden; }
  body {
    background: var(--backdrop);
    font-family: "Open Sans", sans-serif;
    position: relative;
  }
  .card {
    position: absolute;
    width: 620px;
    height: 354px;
    background: var(--card);
    overflow: hidden;
    box-shadow: 0 6px 18px rgba(0,0,0,0.12);
  }
  .card--front { left: 520px; top: 60px; }
  .card--back  { left: 60px;  top: 478px; }

  .stripe {
    position: absolute;
    left: 0; right: 0;
    height: 14px;
    background: var(--teal);
  }
  .stripe--upper { top: 262px; }
  .stripe--lower { top: 296px; }

  /* logo stand-in */
  .brandmark {
    position: absolute;
    display: flex;
    align-items: center;
    gap: 12px;
    color: var(--teal);
    font-weight: 600;
    white-space: nowrap;
  }
  .brandmark__dot {
    border-radius: 50%;
    background: var(--teal);
    flex: none;
  }
  .card--front .brandmark {
    left: 0; right: 0; top: 96px;
    justify-content: center;
    font-size: 34px;
  }
  .card--front .brandmark__dot { width: 30px; height: 30px; }

  .front-name {
    position: absolute;
    left: 0; right: 0; top: 196px;
    text-align: center;
    font-size: 44px;
    font-weight: 400;
    color: var(--ink);
    letter-spacing: 0.5px;
  }

  .card--back .brandmark {
    left: 34px; top: 96px;
    font-size: 24px;
  }
  .card--back .brandmark__dot { width: 22px; height: 22px; }

  .divider {
    position: absolute;
    left: 282px; top: 46px;
    width: 6px; height: 228px;
  }

  .identity {
    position: absolute;
    left: 318px; top: 46px;
  }
  .identity__name {
    font-size: 40px;
    font-weight: 400;
    color: var(--teal);
    line-height: 1;
    letter-spacing: 0.5px;
  }
  .identity__role {
    font-size: 19px;
    color: var(--ink-soft);
    margin-top: 2px;
    letter-spacing: 0.5px;
  }

  .contact {
    position: absolute;
    left: 318px; top: 168px;
    list-style: none;
  }
  .contact__item {
    display: flex;
    align-items: center;
    gap: 12px;
    font-size: 17px;
    color: var(--ink);
    line-height: 26px;
  }
  .contact__icon { width: 15px; height: 15px; flex: none; }
</style>
</head>
<body>

  <section class="card card--front" aria-label="Card front">
    <div class="brandmark">
      <span class="brandmark__dot"></span>
      <span class="brandmark__name">Tom Varulek</span>
    </div>
    <h1 class="front-name">Tom Varulek</h1>
    <div class="stripe stripe--upper"></div>
    <div class="stripe stripe--lower"></div>
  </section>

  <section class="card card--back" aria-label="Card back">
    <div class="brandmark">
      <span class="brandmark__dot"></span>
      <span class="brandmark__name">Tom Varulek</span>
    </div>

    <svg class="divider" viewBox="0 0 6 228" aria-hidden="true">
      <path d="M3 0 L5.5 114 L3 228 L0.5 114 Z" fill="var(--ink)"/>
    </svg>

    <div class="identity">
      <h2 class="identity__name">Tom Varulek</h2>
      <p class="identity__role">web developer</p>
    </div>

    <ul class="contact">
      <li class="contact__item">
        <svg class="contact__icon" viewBox="0 0 16 16" aria-hidden="true">
          <rect width="16" height="16" fill="var(--teal)"/>
          <path d="M5 3.5 L7 5.5 L6 7 Q7 9 9 10 L10.5 9 L12.5 11 L11 12.5 Q7 12.5 3.5 5 Z" fill="#fff"/>
        </svg>
        <span>570-614-3098</span>
      </li>
      <li class="contact__item">
        <svg class="contact__icon" viewBox="0 0 16 16" aria-hidden="true">
          <rect width="16" height="16" fill="var(--teal)"/>
          <circle cx="8" cy="8" r="4.8" fill="none" stroke="#fff" stroke-width="1.3"/>
          <path d="M3.2 8 H12.8 M8 3.2 Q5.5 8 8 12.8 M8 3.2 Q10.5 8 8 12.8" fill="none" stroke="#fff" stroke-width="1"/>
        </svg>
        <span>www.tomvarulek.net</span>
      </li>
      <li class="contact__item">
        <svg class="contact__icon" viewBox="0 0 16 16" aria-hidden="true">
          <rect width="16" height="16" fill="var(--teal)"/>
          <rect x="3" y="4.5" width="10" height="7" fill="none" stroke="#fff" stroke-width="1.2"/>
          <path d="M3 4.5 L8 8.5 L13 4.5" fill="none" stroke="#fff" stroke-width="1.2"/>
        </svg>
        <span>tomvarulek@quillbox.net</span>
      </li>
    </ul>

    <div class="stripe stripe--upper"></div>
    <div class="stripe stripe--lower"></div>
  </section>

</body>
</html>
```